Velcora QXR Magazine Cover style graphic.

I am looking to create a document cover.
Brandle Solutions
What You Really Pay for a Stitching Unitā€
Subtitle: Why the Lowest Upfront Price Can Become the Most Expensive Decision. Using Brandle logo's and Velcora QXR for a high impact cover. It should look like a magazine cover. This is the most advance technology available for the embroidery industry. We want to portray this as a platform and not simply a machine. We will have an 8 page guide.

Target Market(s)

Our customer base

Industry/Entity Type

Industrial Embroidery

Font styles to use
Serif

Colors
0054AA
0677BA
7BADD7
CADEEF
E8F1F8

Requirements
Must have
• High impact, visually pleasing cover.

```html
<!DOCTYPE html>
<html lang="en">
<head>
<meta charset="utf-8">
<title>What You Really Pay for a Stitching Unit – Guide Cover</title>
<link rel="stylesheet" href="https://fonts.googleapis.com/css2?family=Oswald:wght@200;700&family=Poppins:wght@400;700&display=swap">
<style>
  :root {
    --page-bg: #ffffff;
    --cover-black: #050505;
    --accent-blue: #0a9be8;
    --rule-blue: #0677ba;
    --text-white: #ffffff;
    --chrome-light: #ffffff;
    --chrome-mid: #9a9a9a;
    --chrome-dark: #4a4a4a;
    --machine-light: rgba(205,209,212,0.55);
    --machine-mid: rgba(150,155,158,0.35);
    --shirt-purple: rgba(91,42,168,0.55);
  }
  html, body {
    margin: 0;
    padding: 0;
    width: 1200px;
    height: 2821px;
    overflow: hidden;
    background: var(--page-bg);
  }
  .cover {
    position: absolute;
    left: 100px;
    top: 763px;
    width: 1000px;
    height: 1295px;
    overflow: hidden;
    box-shadow: 18px 22px 30px rgba(0,0,0,0.35);
    background:
      radial-gradient(ellipse 60% 22% at 30% 8%, rgba(120,120,120,0.55), transparent 70%),
      radial-gradient(ellipse 70% 30% at 85% 30%, rgba(90,90,90,0.45), transparent 70%),
      radial-gradient(ellipse 80% 25% at 40% 62%, rgba(70,70,70,0.45), transparent 70%),
      radial-gradient(ellipse 60% 30% at 20% 95%, rgba(60,60,60,0.4), transparent 70%),
      var(--cover-black);
  }
  .machine-photo {
    position: absolute;
    left: 520px;
    top: 650px;
    width: 410px;
    height: 565px;
    z-index: 0;
    background:
      radial-gradient(ellipse 32% 14% at 22% 40%, var(--shirt-purple), transparent 80%),
      linear-gradient(180deg, var(--machine-light) 0%, var(--machine-mid) 65%, rgba(120,125,128,0) 100%);
    border-radius: 4px;
  }
  .title { margin: 0; position: relative; z-index: 1; }
  .title-intro {
    position: absolute;
    left: 114px;
    top: 106px;
    font-family: "Oswald", sans-serif;
    font-weight: 200;
    font-size: 84px;
    line-height: 85px;
    color: var(--accent-blue);
    text-transform: uppercase;
    letter-spacing: -1px;
    white-space: nowrap;
  }
  .title-main {
    position: absolute;
    left: 112px;
    top: 380px;
    font-family: "Oswald", sans-serif;
    font-weight: 700;
    font-size: 132px;
    line-height: 122px;
    text-transform: uppercase;
    letter-spacing: -2px;
    white-space: nowrap;
    background: linear-gradient(180deg, var(--chrome-light) 0%, var(--chrome-mid) 45%, var(--chrome-dark) 55%, var(--chrome-light) 100%);
    background-size: 100% 122px;
    -webkit-background-clip: text;
    background-clip: text;
    color: transparent;
  }
  .side-rule {
    position: absolute;
    left: 117px;
    top: 646px;
    width: 2px;
    height: 649px;
    background: var(--rule-blue);
  }
  .subtitle {
    position: absolute;
    left: 158px;
    top: 670px;
    margin: 0;
    z-index: 1;
    font-family: "Poppins", sans-serif;
    font-weight: 400;
    font-size: 26px;
    line-height: 36px;
    color: var(--text-white);
  }
  .subtitle strong {
    font-weight: 700;
    color: var(--accent-blue);
  }
  .maker-name {
    position: absolute;
    left: 166px;
    top: 1005px;
    font-family: "Poppins", sans-serif;
    font-weight: 700;
    font-size: 36px;
    color: var(--text-white);
  }
  .dealer-name {
    position: absolute;
    left: 166px;
    top: 1112px;
    display: flex;
    align-items: center;
    gap: 12px;
    font-family: "Poppins", sans-serif;
    font-weight: 700;
    font-size: 28px;
    line-height: 30px;
    color: var(--text-white);
  }
  .dealer-mark {
    width: 54px;
    height: 54px;
    background: var(--rule-blue);
  }
</style>
</head>
<body>
  <main class="cover">
    <div class="machine-photo" role="img" aria-label="Photo of a multi-needle industrial embroidery machine on a stand with a purple shirt hooped under the needles and a touchscreen control panel"></div>
    <h1 class="title">
      <span class="title-intro">What You<br>Really Pay<br>For A</span>
      <span class="title-main">Stitching<br>Unit</span>
    </h1>
    <div class="side-rule"></div>
    <p class="subtitle">Why the <strong>Lowest<br>Upfront</strong> Price<br>Can Become the<br><strong>Most Expensive<br>Decision</strong></p>
    <div class="maker-name">Velcora</div>
    <div class="dealer-name"><span class="dealer-mark"></span><span>Brandle<br>Solutions</span></div>
  </main>
</body>
</html>
```